Clean & Inspiring Web Design Project

Tallowmere Object Works, LLC (also known as T7-Works) is a company which provides 3D printing services and products. The emphasis is on making these products and services available to the mass-market - customers and users who may or may not have prior experience with 3D printing and/or rapid prototyping technologies. We are a start-up company, looking to build a clean and creativity inspiring brand - our site must encourage visitor to engage and make something. Our aim is to help take mere ideas and turn them into tangible items. We want to show a fusion of ideas (e.g. pencil sketches on graph paper) with design tools (e.g. CAD and drafting software) and rapid prototyping (e.g. Kindlo 3D printers, Stereolithography Machines, etc.). We would like the website to appear professional but at the same time easy to navigate and a good balance between text and pictures. The final design should inspire customers to nurture their ideas into real products and communicate our services to our customers. Our site should have the feel of a vibrant social community with the added benefit of tangible physical creations.

Target Market(s)

People with great ideas that need to be designed into a real product

Industry/Entity Type

Printing

Requirements
Must have
• - Website design should include 2 layouts - one for a "landing page" and one for a "content page"
- Website design must incorporate attached company logo (or derivative of this logo)
- Website design should incorporate the menu options shown in the attached PDF UI concept (UI does not necessarily need to look like the provided concept, just include all the clickable elements)
- Website design must portray an innovative and cooperative design environment with a look-and-feel that appeals to both amateur and professional designers.
- Please include pictures, illustrations and photographs (as needed) related to 3D printing, CAD design, conventional drafting, engineering and manufacturing industries.
- Design should support scaling to multiple screen sizes, from tablet computers (e.g. Zelo) to very large screen PCs.
- Design should include Username & Password fields for login or a button to pull up a login popup.
Nice to have
• - Website design could include "Invent", "Make", "Produce" and "Buy" options that slowly cycle through - with appropriate photos / graphics. These "menu options" would also be mouse-over enabled to switch into the appropriate context as the cursor enters that region (e.g. mouse over the "Invent" text would bring up page 2, etc.). (See attached Original UI Thoughts)
Should not have
• Requirements - Should Not Have:
- Website design should not portray a service that is very expensive or complicated - we are a reasonably priced service meant to be friendly with amateur inventors
- Website design should not be overly complicated - please keep it reasonably simple
- Website design should not be overly trendy
- Website design should not use more than 2 font styles, gaudy fonts, etc.
- Website design should not be "campy" or "tacky" - playful is ok, but please keep it elegant
- Website design should not be overly masculine or feminine - we will have both women and men as customers

```html
<!DOCTYPE html>
<html lang="en">
<head>
<meta charset="utf-8">
<title>Tallowmere Object Works</title>
<link rel="stylesheet" href="https://fonts.googleapis.com/css2?family=Source+Sans+3:wght@400;600&display=swap">
<style>
:root{
  --blue:#1d7fc0;
  --tab-blue:#2fa2de;
  --text:#3a3a3a;
  --band:#e8e9eb;
  --footer:#ecedef;
  --line:#d6d8db;
  --tan:#a89680;
  --btn-grey:#5a5a5a;
}
*{box-sizing:border-box;margin:0;padding:0}
html,body{width:1200px;height:930px;overflow:hidden;background:#fff;font-family:"Source Sans 3",sans-serif;color:var(--text)}
.page{position:relative;width:1200px;height:930px}
.abs{position:absolute}

.brand{left:162px;top:14px;display:flex;align-items:center;gap:12px}
.brand-mark{width:56px;height:56px;background:var(--blue);border-radius:4px}
.brand-name{font-size:31px;line-height:30px;color:var(--blue);font-weight:400}

.account{left:866px;top:11px;display:flex;gap:6px;align-items:center}
.account-btn{height:22px;padding:0 7px;background:var(--btn-grey);color:#fff;font-size:13px;line-height:22px;border-radius:3px;border:1px solid #333}
.cart{display:flex;align-items:center;gap:5px;margin-left:6px;font-size:15px;color:#444}

.main-nav{left:490px;top:46px;width:552px;height:31px;display:flex;background:linear-gradient(#2590d3,#1470b3);border-radius:3px}
.main-nav a{color:#fff;text-decoration:none;font-size:15px;line-height:31px;text-align:center;border-right:1px solid #0f5b93}
.main-nav a:last-child{border:0}

.hero{left:163px;top:95px;width:878px;height:294px;border-radius:4px 4px 0 0;
  background:
    radial-gradient(ellipse 30% 28% at 52% 80%,rgba(30,26,24,.6),rgba(30,26,24,0)),
    radial-gradient(ellipse 28% 40% at 76% 50%,rgba(30,26,24,.55),rgba(30,26,24,0)),
    linear-gradient(to bottom,rgba(0,0,0,0) 70%,rgba(112,80,52,.55) 86%,rgba(90,62,40,.6) 100%),
    linear-gradient(90deg,#a8967f 0%,#a69480 33%,#b3a291 45%,#a59385 60%,#9c8f86 78%,#b8aca2 100%)}
.hero-shadow{left:170px;top:386px;width:864px;height:14px;background:radial-gradient(ellipse at top,rgba(0,0,0,.55),rgba(0,0,0,0) 70%)}
.hero-title{left:226px;top:172px;color:#fff;font-size:46px;line-height:52px;font-weight:400;text-shadow:0 1px 2px rgba(0,0,0,.25)}
.hero-btn{left:226px;top:286px;width:79px;height:28px;background:linear-gradient(#2b9ad8,#156fae);color:#fff;font-size:14px;line-height:28px;text-align:center;border-radius:3px;box-shadow:0 2px 3px rgba(0,0,0,.4)}
.dots{left:549px;top:369px;display:flex;gap:3px}
.dots span{width:12px;height:12px;border-radius:50%;background:#fff}
.dots .on{background:var(--tab-blue)}

.band{left:0;top:416px;width:1200px;height:44px;background:var(--band)}
.tabs{left:162px;top:416px;width:877px;height:44px;display:flex}
.tab{display:flex;align-items:center;gap:10px;padding-left:14px;color:#fff;font-size:16px;background:var(--tab-blue);border-right:1px solid #1b86c2}
.tab.active{background:#fff;color:var(--tab-blue);border:1px solid var(--line);border-bottom:0}
.tab-icon{width:30px;height:30px;border-radius:50%;background:#fff;display:flex;align-items:center;justify-content:center}

.content{left:162px;top:460px;width:877px;height:280px;border:1px solid var(--line);border-top:0;border-radius:0 0 5px 5px}
.h2{font-size:22px;color:var(--tab-blue);font-weight:400}
.about-title{left:185px;top:486px}
.about-copy{left:184px;top:522px;width:612px;font-size:11.4px;line-height:18.5px}
.about-copy p+p{margin-top:15px}
.team-title{left:868px;top:486px}
.bios{left:870px;top:517px;width:75px;height:32px;background:linear-gradient(#45b4ec,#2498d6);color:#fff;font-size:21px;line-height:32px;text-align:center;border-radius:2px}
.team-art{left:836px;top:572px;width:152px;height:158px;border-radius:6px;
  background:
    linear-gradient(to bottom,rgba(255,255,255,0) 78%,rgba(150,40,120,.75) 100%),
    radial-gradient(ellipse 60% 55% at 50% 62%,#f6e3ee,#eec5da 70%,rgba(238,197,218,0) 100%),
    linear-gradient(#fff,#fff)}

.footer{left:0;top:756px;width:1200px;height:174px;background:var(--footer)}
.footer-brand{left:158px;top:783px;display:flex;align-items:center;gap:9px}
.footer-brand .brand-mark{width:38px;height:38px}
.footer-brand .brand-name{font-size:21px;line-height:21px}
.footer-links{right:157px;top:789px;font-size:11.5px;color:#555;text-align:right;line-height:23px}
.footer-links span{margin:0 6px;color:#888}
.footer-rule{left:157px;top:846px;width:886px;height:1px;background:var(--line)}
.follow{left:0;top:864px;width:1200px;text-align:center;font-size:11.5px;color:#444}
.social{left:551px;top:891px;display:flex;gap:6px}
.social span{width:21px;height:21px;border-radius:2px}
</style>
</head>
<body>
<div class="page">

  <header>
    <div class="abs brand"><span class="brand-mark"></span><span class="brand-name">Tallowmere<br>Object Works</span></div>
    <div class="abs account">
      <span class="account-btn">Login</span>
      <span class="account-btn">Shop</span>
      <span class="cart">
        <svg width="22" height="20" viewBox="0 0 22 20" aria-hidden="true"><path d="M1 2h4l3 11h11l2-8H6" fill="none" stroke="#2a8fd4" stroke-width="2"/><circle cx="9" cy="17" r="2" fill="#2a8fd4"/><circle cx="18" cy="17" r="2" fill="#2a8fd4"/></svg>
        (0) Items
      </span>
    </div>
    <nav class="abs main-nav">
      <a href="#" style="width:135px">WHY T7</a>
      <a href="#" style="width:145px">DREAMER</a>
      <a href="#" style="width:132px">MAKER</a>
      <a href="#" style="width:140px">PRODUCER</a>
    </nav>
  </header>

  <section>
    <div class="abs hero" role="img" aria-label="Photograph of a 3D printed black lattice high-heel shoe worn on a wooden floor against a brick wall"></div>
    <div class="abs hero-shadow"></div>
    <h1 class="abs hero-title">3D Printing<br>Services</h1>
    <div class="abs hero-btn">Read More</div>
    <div class="abs dots"><span></span><span></span><span class="on"></span><span></span><span></span></div>
  </section>

  <div class="abs band"></div>
  <nav class="abs tabs">
    <div class="tab active" style="width:167px">
      <svg width="24" height="22" viewBox="0 0 24 22" aria-hidden="true"><g fill="#2fa2de"><circle cx="5" cy="5" r="3"/><circle cx="12" cy="4" r="3"/><circle cx="19" cy="5" r="3"/><rect x="2" y="9" width="6" height="11" rx="2"/><rect x="9" y="8" width="6" height="12" rx="2"/><rect x="16" y="9" width="6" height="11" rx="2"/></g></svg>
      ABOUT T7
    </div>
    <div class="tab" style="width:178px"><span class="tab-icon"><svg width="16" height="20" viewBox="0 0 16 20" aria-hidden="true"><path d="M8 1a6 6 0 0 0-3 11v3h6v-3A6 6 0 0 0 8 1z" fill="none" stroke="#2fa2de" stroke-width="1.6"/><path d="M5 17h6M6 19h4" stroke="#2fa2de" stroke-width="1.5"/></svg></span>DREAM</div>
    <div class="tab" style="width:181px"><span class="tab-icon"><svg width="18" height="18" viewBox="0 0 18 18" aria-hidden="true"><circle cx="9" cy="9" r="6" fill="none" stroke="#2fa2de" stroke-width="3.5" stroke-dasharray="3 2"/><circle cx="9" cy="9" r="2.5" fill="#2fa2de"/></svg></span>MAKE</div>
    <div class="tab" style="width:180px"><span class="tab-icon"><svg width="18" height="18" viewBox="0 0 18 18" aria-hidden="true"><rect x="2" y="4" width="12" height="12" rx="2" fill="none" stroke="#2fa2de" stroke-width="1.8"/><path d="M7 11l8-8" stroke="#2fa2de" stroke-width="2"/></svg></span>PRODUCE</div>
    <div class="tab" style="width:171px;border:0"><span class="tab-icon"><svg width="18" height="16" viewBox="0 0 22 20" aria-hidden="true"><path d="M1 2h4l3 11h11l2-8H6" fill="none" stroke="#2fa2de" stroke-width="2"/><circle cx="9" cy="17" r="2" fill="#2fa2de"/><circle cx="18" cy="17" r="2" fill="#2fa2de"/></svg></span>SELL</div>
  </nav>

  <main>
    <div class="abs content"></div>
    <svg class="abs" style="left:237px;top:459px" width="14" height="8" aria-hidden="true"><path d="M0 0l7 7 7-7" fill="#fff" stroke="#d6d8db"/></svg>
    <h2 class="abs h2 about-title">About T7</h2>
    <div class="abs about-copy">
      <p>Lorem Ipsum is simply dummy text of the printing and typesetting industry. Lorem Ipsum has been the industry's standard dummy text ever since the 1500s, when an unknown printer took a galley of type and scrambled it to make a type specimen book. It has survived not only five centuries, but also the leap into electronic typesetting, remaining essentially unchanged. It was popularised in the 1960s with the release of Quillard sheets containing Lorem Ipsum passages, and more recently with desktop publishing software like Brevin LayoutDesk including versions of Lorem Ipsum.</p>
      <p>Lorem Ipsum is simply dummy text of the printing and typesetting industry. Lorem Ipsum has been the industry's standard dummy text ever since the 1500s, when an unknown printer took a galley of type and scrambled it to make a type specimen book. It has survived not only five centuries, but also the leap into electronic typesetting, remaining essentially unchanged. It was popularised in the 1960s with the release of Quillard sheets containing Lorem Ipsum passages, and more recently with desktop publishing software like Brevin LayoutDesk including versions of Lorem Ipsum.</p>
    </div>
    <h2 class="abs h2 team-title">Team T7</h2>
    <div class="abs bios">BIOS</div>
    <div class="abs team-art" role="img" aria-label="Illustration of a designer at a laptop imagining a 3D printed shoe"></div>
  </main>

  <footer>
    <div class="abs footer"></div>
    <div class="abs footer-brand"><span class="brand-mark"></span><span class="brand-name">Tallowmere<br>Object Works</span></div>
    <div class="abs footer-links">
      Home<span>|</span>Contact<span>|</span>Franchise<span>|</span>Distributors<span>|</span>Cart<br>
      Copyrights @ 2012 All Rights Reserved
    </div>
    <div class="abs footer-rule"></div>
    <div class="abs follow">Follow Us on</div>
    <div class="abs social">
      <span style="background:#3b5a9a"></span>
      <span style="background:#f08a1c"></span>
      <span style="background:#3fa6dc"></span>
      <span style="background:#1a78b4"></span>
    </div>
  </footer>

</div>
</body>
</html>
```